Modern Business Card For A Digital Advertising Company

I'll be print on the Pell Prints Velour paper http://us.pellprints.com/products/velour/business-cards.html
Need's to be modern and use the color palette of the logo or gray scales. I think integrating the pixelation of the logo in to the card and having it wrap from one side to the other could be interesting. My company provides ad operations, web development, and number of other services to websites around the world. You can see my website at http://www.zantorhq.com
Contact info on the card needs to have
Owen Lasko
President
p.318.204.6637
owen@zantorhq.com
http://www.zantorhq.com
Doesn't necessarily need to be in that order
Website owners
Business

```html
<!DOCTYPE html>
<html lang="en">
<head>
<meta charset="utf-8">
<title>Owen Lasko – Zantor HQ Business Card</title>
<link href="https://fonts.googleapis.com/css2?family=Open+Sans:ital,wght@0,400;0,600;0,700;1,400&display=swap" rel="stylesheet">
<style>
  :root {
    --backdrop-top: #8f8f8f;
    --backdrop-bottom: #000000;
    --card-dark: #8a8a8a;
    --card-light: #e4e4e4;
    --panel-white: #ffffff;
    --ink: #111111;
    --brand-green: #8cc63f;
    --icon-disc: #141414;
  }
  * { margin: 0; padding: 0; box-sizing: border-box; }
  html, body {
    width: 1200px;
    height: 911px;
    overflow: hidden;
  }
  body {
    position: relative;
    background: linear-gradient(to bottom, var(--backdrop-top) 0%, #4a4a4a 40%, var(--backdrop-bottom) 78%);
    font-family: "Open Sans", Arial, sans-serif;
    color: var(--ink);
  }
  .card-shapes {
    position: absolute;
    left: 0;
    top: 0;
  }
  .card-text { position: absolute; white-space: nowrap; }
  .holder-name {
    left: 248px; top: 162px;
    font-size: 62px; font-weight: 700; letter-spacing: -1px;
  }
  .holder-title {
    left: 366px; top: 224px;
    font-size: 28px; font-style: italic; font-weight: 400;
  }
  .contact-phone {
    left: 308px; top: 300px;
    font-size: 44px; font-weight: 600;
  }
  .contact-email {
    left: 312px; top: 373px;
    font-size: 26px; font-weight: 600;
  }
  .contact-web {
    left: 248px; top: 458px;
    font-size: 31px; font-weight: 600;
  }
  .brand-mark {
    position: absolute;
    left: 706px; top: 170px;
    width: 290px;
    display: flex; flex-direction: column; align-items: center;
  }
  .brand-square {
    width: 190px; height: 190px;
    background: var(--brand-green);
  }
  .brand-name {
    margin-top: 34px;
    font-size: 52px; font-weight: 700;
    color: var(--brand-green);
    letter-spacing: 2px;
    white-space: nowrap;
  }
</style>
</head>
<body>
  <svg class="card-shapes" width="1200" height="911" viewBox="0 0 1200 911" aria-hidden="true">
    <defs>
      <linearGradient id="cardBase" x1="0" y1="0" x2="1" y2="1">
        <stop offset="0" stop-color="#f0f0f0"/>
        <stop offset="0.5" stop-color="#a9a9a9"/>
        <stop offset="1" stop-color="#d6d6d6"/>
      </linearGradient>
      <linearGradient id="panelFace" x1="0" y1="0" x2="1" y2="0">
        <stop offset="0" stop-color="#a4a4a4"/>
        <stop offset="0.35" stop-color="#f6f6f6"/>
        <stop offset="1" stop-color="#ffffff"/>
      </linearGradient>
      <linearGradient id="lowerBand" x1="0" y1="0" x2="1" y2="0">
        <stop offset="0" stop-color="#ffffff"/>
        <stop offset="0.5" stop-color="#c9c9c9"/>
        <stop offset="1" stop-color="#f4f4f4"/>
      </linearGradient>
      <linearGradient id="stripFace" x1="0" y1="0" x2="0" y2="1">
        <stop offset="0" stop-color="#dcdcdc"/>
        <stop offset="0.5" stop-color="#9a9a9a"/>
        <stop offset="1" stop-color="#c8c8c8"/>
      </linearGradient>
    </defs>

    <rect class="card-base" x="67" y="107" width="1085" height="622" fill="url(#cardBase)"/>
    <path class="card-left-wing" d="M67,107 Q160,110 168,200 V600 Q175,690 280,712 H67 Z" fill="#bdbdbd"/>
    <path class="card-upper-panel" d="M170,137 H1020 Q1130,137 1132,250 V556 H178 Q170,556 170,540 Z" fill="url(#panelFace)"/>
    <path class="card-lower-band" d="M176,560 H1110 Q1140,560 1145,620 L1152,729 Q1080,690 1040,688 H300 Q200,688 176,600 Z" fill="url(#lowerBand)"/>

    <rect class="accent-strip" x="67" y="172" width="190" height="54" fill="url(#stripFace)"/>
    <rect class="accent-strip" x="67" y="300" width="200" height="52" fill="url(#stripFace)"/>
    <rect class="accent-strip" x="67" y="365" width="200" height="52" fill="url(#stripFace)"/>

    <g class="icon-phone">
      <circle cx="268" cy="326" r="27" fill="#8a8a8a"/>
      <circle cx="271" cy="326" r="25" fill="var(--icon-disc)"/>
      <rect x="259" y="308" width="24" height="36" rx="4" fill="none" stroke="#ffffff" stroke-width="3"/>
      <rect x="263" y="313" width="16" height="23" fill="#ffffff"/>
    </g>
    <g class="icon-email">
      <circle cx="268" cy="391" r="27" fill="#8a8a8a"/>
      <circle cx="271" cy="391" r="25" fill="var(--icon-disc)"/>
      <text x="271" y="402" text-anchor="middle" font-family="Open Sans, Arial, sans-serif" font-size="32" font-weight="600" fill="#ffffff">@</text>
    </g>
  </svg>

  <div class="card-text holder-name">Owen Lasko</div>
  <div class="card-text holder-title">President</div>
  <div class="card-text contact-phone">318.204.6637</div>
  <div class="card-text contact-email">owen@zantorhq.com</div>
  <div class="card-text contact-web">www.zantorhq.com</div>

  <div class="brand-mark">
    <div class="brand-square"></div>
    <div class="brand-name">ZANTOR HQ</div>
  </div>
</body>
</html>
```